Coastline Premier Retreats Business Card Design

Design a business card for Coastline Premier Retreats. Look at the website for colors and reference. Card should have logo, name, title, office number, mobile number, email, URL and a tagline like, "Luxury Hotel & Resort Email Marketing" (This might change).

https://www.coastlinepremierretreats.example

The rest I will leave up to your imagination.

Contact Information for Business Card

Logo, name, title, office number, mobile number, email, URL and a tagline like, "Luxury Hotel & Resort Email Marketing" (This might change).

```html
<!DOCTYPE html>
<html lang="en">
<head>
<meta charset="utf-8">
<title>Coastline Premier Retreats – Business Card</title>
<link rel="stylesheet" href="https://fonts.googleapis.com/css2?family=Open+Sans:wght@400;600;700;800&display=swap">
<style>
  :root {
    --backdrop: #242424;
    --card-dark: #1e1e21;
    --card-fold: #26262a;
    --accent: #f07a1a;
    --ink-light: #ffffff;
    --ink-dark: #151515;
    --sky: #b9cfe0;
    --sea: #7fc2c6;
    --foliage: #8c9a6a;
  }
  * { box-sizing: border-box; margin: 0; padding: 0; }
  html, body {
    width: 1200px; height: 780px; overflow: hidden;
    background: var(--backdrop);
    font-family: "Open Sans", Arial, sans-serif;
  }
  .canvas { position: relative; width: 1200px; height: 780px; }

  .card {
    position: absolute;
    width: 540px; height: 309px;
    border-radius: 2px;
    overflow: hidden;
    box-shadow: 0 14px 30px rgba(0,0,0,.55);
  }

  /* Front */
  .card-front { left: 60px; top: 60px; }
  .front-photo {
    position: absolute; inset: 0;
    background: linear-gradient(180deg, var(--sky) 0%, #cfdce6 28%, var(--sea) 52%, var(--foliage) 78%, #7d8a60 100%);
  }
  .front-brand {
    position: absolute; left: 0; right: 0; top: 50%;
    transform: translateY(-50%);
    text-align: center;
    font-weight: 800; font-size: 34px; letter-spacing: .5px;
    color: var(--ink-dark);
  }

  /* Back */
  .card-back { left: 600px; top: 411px; background: var(--card-dark); }
  .back-fold { position: absolute; inset: 0; }
  .back-brand {
    position: absolute; left: 34px; top: 44px;
    display: flex; align-items: center; gap: 10px;
    font-weight: 800; font-size: 19px; color: var(--ink-light);
  }
  .back-brand .brand-square { width: 12px; height: 12px; background: var(--accent); }

  .contact {
    position: absolute; right: 30px; top: 60px;
    text-align: right; color: var(--ink-light);
  }
  .person-name { font-size: 25px; font-weight: 800; line-height: 1.1; }
  .person-name .first { color: var(--accent); }
  .person-title { font-size: 12px; font-weight: 600; margin-top: 2px; }
  .tagline { color: var(--accent); font-size: 12px; line-height: 1.35; margin-top: 10px; }
  .contact-list { list-style: none; margin-top: 10px; font-size: 12px; line-height: 1.55; }
  .contact-list li { display: flex; justify-content: flex-end; align-items: center; gap: 7px; }
  .contact-list svg { width: 11px; height: 11px; flex: none; }
</style>
</head>
<body>
<main class="canvas">

  <section class="card card-front" aria-label="Card front">
    <div class="front-photo" role="img" aria-label="Photograph of a rocky coastal cove with turquoise water framed by cypress trees"></div>
    <div class="front-brand">Coastline Premier Retreats</div>
  </section>

  <section class="card card-back" aria-label="Card back">
    <svg class="back-fold" viewBox="0 0 540 309" preserveAspectRatio="none" aria-hidden="true">
      <defs>
        <linearGradient id="foldShade" x1="0" y1="0" x2="1" y2="0">
          <stop offset="0" stop-color="#1e1e21"/>
          <stop offset="1" stop-color="#2a2a2e"/>
        </linearGradient>
      </defs>
      <polygon points="0,0 345,0 140,309 0,309" fill="url(#foldShade)"/>
      <line x1="345" y1="0" x2="140" y2="309" stroke="#151517" stroke-width="2"/>
    </svg>

    <div class="back-brand"><span class="brand-square"></span>Coastline Premier Retreats</div>

    <div class="contact">
      <h1 class="person-name"><span class="first">Lena</span> Marwick</h1>
      <p class="person-title">Co-Founder</p>
      <p class="tagline">Luxury Hotel &amp;<br>Resort Email Marketing</p>
      <ul class="contact-list">
        <li>(555) 014-2758
          <svg viewBox="0 0 12 12"><path d="M2.5 1l2 2-1 1.3a6 6 0 0 0 4.2 4.2L9 7.5l2 2-1.3 1.5C5.5 11 1 6.5 1 2.3z" fill="var(--accent)"/></svg></li>
        <li>(555) 019-7777
          <svg viewBox="0 0 12 12"><rect x="3" y="0.8" width="6" height="10.4" rx="1" fill="none" stroke="var(--accent)" stroke-width="1.2"/></svg></li>
        <li>www.coastlinepremierretreats.example
          <svg viewBox="0 0 12 12"><circle cx="6" cy="6" r="5" fill="none" stroke="var(--accent)" stroke-width="1.2"/><path d="M1 6h10M6 1c-2.5 3-2.5 7 0 10M6 1c2.5 3 2.5 7 0 10" fill="none" stroke="var(--accent)" stroke-width="1"/></svg></li>
        <li>info@coastlinepremierretreats.example
          <svg viewBox="0 0 12 12"><rect x="0.8" y="2.5" width="10.4" height="7.5" fill="none" stroke="var(--accent)" stroke-width="1.2"/><path d="M1 3l5 4 5-4" fill="none" stroke="var(--accent)" stroke-width="1.2"/></svg></li>
      </ul>
    </div>
  </section>

</main>
</body>
</html>
```